Hollow Mesa Farm Vault Reserve Wine Label (Front and Back)

I need to create an elite tier wine label.  I would like it to be in a light, natural color with silver or gold.  I would like it to look rich and expensive, mostly monochromatic, elegantly simple.  It will need to stand up next to wine labels that are black and charcoal colored and look like the more expensive wine of the 3.  I have attached a similar label that it will be grouped with and some instructions.
We are a winery in southeast Washington state with a reputation for fine wines and top notch terroir.  We want to present family, tradition and high value wine in the bottle.

```html
<!DOCTYPE html>
<html lang="en">
<head>
<meta charset="utf-8">
<title>Hollow Mesa Farm – Vault Reserve Label Options</title>
<link rel="stylesheet" href="https://fonts.googleapis.com/css2?family=Cinzel:wght@400;500&family=Gelasio:wght@400&family=Lora&family=Pinyon+Script&family=Roboto+Condensed:wght@400;700&display=swap">
<style>
:root{
  --page:#ffffff;
  --silver-bg:#f3f4f6;
  --cream-bg:#f8f8ec;
  --silver-ink:#a7aaae;
  --silver-soft:#b9bcc0;
  --black-ink:#2b2b2b;
  --body-ink:#555555;
  --caption-ink:#111111;
  --band-dark:#b4b5b8;
  --band-light:#f1f1f2;
  --barcode-yellow:#f0e81a;
  --scene-dark:#2a1208;
  --scene-mid:#6b2c0c;
  --scene-glow:#b55a1c;
}
*{box-sizing:border-box;margin:0;padding:0}
html,body{width:1200px;height:3927px;overflow:hidden;background:var(--page)}
.board{position:relative;width:1200px;height:3927px}
.option{position:relative;width:1200px;height:982px;overflow:hidden}
.option-caption{position:absolute;left:58px;top:44px;width:470px;font:400 27px/33px "Lora",serif;color:var(--caption-ink)}
.bottle-scene{position:absolute;left:546px;top:0;width:654px;height:982px;
  background:radial-gradient(ellipse at 60% 45%,var(--scene-glow) 0%,var(--scene-mid) 45%,var(--scene-dark) 100%)}

/* front label */
.front-label{position:absolute;left:58px;top:149px;width:349px;height:583px;background:var(--label-bg)}
.front-frame{position:absolute;left:11px;top:11px;right:11px;height:519px;border:1px solid #d9dadc}
.front-label .line{position:absolute;left:0;width:100%;text-align:center;white-space:nowrap}
.brand-name{font:400 37px/1 "Cinzel",serif;letter-spacing:0}
.estate{font:400 14px/1 "Gelasio",serif;letter-spacing:2px;color:var(--silver-ink)}
.tier-script{font:400 38px/1 "Pinyon Script",cursive;color:var(--silver-ink)}
.varietal{font:400 21px/1 "Cinzel",serif;letter-spacing:2px}
.region{font:400 13px/1 "Gelasio",serif;letter-spacing:2px;color:var(--silver-ink)}
.vintage{font:400 14px/1 "Gelasio",serif;letter-spacing:1px;color:var(--silver-ink)}
.mark{position:absolute;left:50%;top:255px;width:140px;height:140px;margin-left:-70px;border:3px solid var(--silver-soft);
  display:flex;align-items:center;justify-content:center;text-align:center;
  font:400 17px/22px "Cinzel",serif;color:var(--silver-ink);letter-spacing:1px}
.heritage-band{position:absolute;left:0;top:537px;width:100%;height:46px;
  background:linear-gradient(90deg,var(--band-dark),var(--band-light) 70%,var(--band-dark));
  font:400 11px/46px "Gelasio",serif;letter-spacing:.6px;color:#333;text-align:center}

.ink-black .brand-name,.ink-black .varietal{color:var(--black-ink)}
.ink-silver .brand-name,.ink-silver .varietal{color:var(--silver-ink)}
.bg-silver{--label-bg:var(--silver-bg)}
.bg-cream{--label-bg:var(--cream-bg)}

/* back label */
.back-label{position:absolute;left:407px;top:386px;width:401px;height:465px;background:var(--label-bg)}
.back-title{position:absolute;left:24px;top:24px;font:400 29px/1 "Cinzel",serif;color:var(--silver-soft);white-space:nowrap}
.back-sub{position:absolute;left:24px;top:62px;width:353px;display:flex;justify-content:space-between;
  font:400 13px/1 "Gelasio",serif;letter-spacing:2px;color:var(--silver-ink)}
.back-rule{position:absolute;left:20px;top:81px;width:361px;height:1px;background:#cfd0d2}
.back-story{position:absolute;left:24px;top:90px;width:353px;font:400 11.4px/14.4px "Gelasio",serif;color:var(--body-ink);text-align:justify}
.signoff{position:absolute;left:24px;font:400 11px/16px "Gelasio",serif;color:var(--body-ink)}
.signoff .sig{font:400 14px/1 "Pinyon Script",cursive;color:#666}
.crest{position:absolute;left:252px;top:209px;width:125px;height:119px;
  background:radial-gradient(circle,#c9cacc 0%,#e6e7e8 70%,transparent 72%)}
.legal-panel{position:absolute;left:0;top:331px;width:100%;height:134px;background:#ffffff}
.warning{position:absolute;left:8px;top:4px;width:190px;font:400 9.2px/12.8px "Roboto Condensed",sans-serif;color:#111;text-transform:uppercase}
.warning b,.legal-right b{font-weight:700}
.legal-right{position:absolute;right:9px;top:4px;width:200px;text-align:right;font:400 9.2px/12.8px "Roboto Condensed",sans-serif;color:#111;text-transform:uppercase}
.legal-right .produced{margin-top:6px}
.barcode-slot{position:absolute;left:198px;top:58px;width:200px;height:64px;background:var(--barcode-yellow);
  font:400 11px/64px "Roboto Condensed",sans-serif;color:#222;text-align:center;text-transform:uppercase}
</style>
</head>
<body>
<main class="board">

<section class="option bg-silver ink-black">
  <p class="option-caption">option 1: silver background, silver lettering with black accents</p>
  <div class="bottle-scene" role="img" aria-label="Photo of the wine bottle wearing the label on a wooden table"></div>
  <div class="front-label">
    <div class="front-frame"></div>
    <div class="line brand-name" style="top:66px">Hollow Mesa</div>
    <div class="line brand-name" style="top:117px">Farm</div>
    <div class="line estate" style="top:174px">ESTATE VINEYARD</div>
    <div class="line tier-script" style="top:203px">Vault Reserve</div>
    <div class="mark">Hollow<br>Mesa<br>Farm</div>
    <div class="line varietal" style="top:438px">CABERNET SAUVIGNON</div>
    <div class="line region" style="top:474px">HORSE HEAVEN HILLS</div>
    <div class="line vintage" style="top:494px">2022</div>
    <div class="heritage-band">FAMILY STEWARDS OF THE LAND FOR 5 GENERATIONS</div>
  </div>
  <div class="back-label">
    <div class="back-title">HOLLOW MESA FARM</div>
    <div class="back-sub"><span>VAULT RESERVE</span><span>CABERNET SAUVIGNON</span></div>
    <div class="back-rule"></div>
    <p class="back-story">Hollow Mesa Farm wines are exclusively sourced from our family's Estate Vineyard in the Horse Heaven Hills of Washington state. For five generations, we have cultivated this rugged and fertile land, embodying our deep-seated love and dedication. We believe that exceptional wine is the result of outstanding vineyards, limited production, and astute winemaking. With the utmost pride and joy, we present this exquisite Cabernet Sauvignon from our ranch to your table.</p>
    <p class="signoff" style="top:226px">Cheers, <span class="sig">Mara Lindqvist</span><br>Mara Lindqvist, Winemaker</p>
    <p class="signoff" style="top:269px">Cheers, <span class="sig">Tom Hadley</span><br>Tom Hadley, Farmer &amp; Proprietor</p>
    <div class="crest" role="img" aria-label="Family crest illustration"></div>
    <div class="legal-panel">
      <p class="warning"><b>Government warning:</b> (1) According to the Surgeon General, women should not drink alcoholic beverages during pregnancy because of the risk of birth defects. (2) Consumption of alcoholic beverages impairs your ability to drive a car or operate machinery, and may cause health problems.</p>
      <div class="legal-right"><b>750 ML</b> contains sulfites<br>15% alc. by vol.<p class="produced"><b>Produced and bottled by:</b> Hadley Wine Estates, LLC, Prosser WA, USA</p></div>
      <div class="barcode-slot">Bar code placeholder</div>
    </div>
  </div>
</section>

<section class="option bg-silver ink-silver">
  <p class="option-caption" style="left:56px">option 2: silver background, all silver lettering</p>
  <div class="bottle-scene" role="img" aria-label="Photo of the wine bottle wearing the label on a wooden table"></div>
  <div class="front-label">
    <div class="front-frame"></div>
    <div class="line brand-name" style="top:66px">Hollow Mesa</div>
    <div class="line brand-name" style="top:117px">Farm</div>
    <div class="line estate" style="top:174px">ESTATE VINEYARD</div>
    <div class="line tier-script" style="top:203px">Vault Reserve</div>
    <div class="mark">Hollow<br>Mesa<br>Farm</div>
    <div class="line varietal" style="top:438px">CABERNET SAUVIGNON</div>
    <div class="line region" style="top:474px">HORSE HEAVEN HILLS</div>
    <div class="line vintage" style="top:494px">2022</div>
    <div class="heritage-band">FAMILY STEWARDS OF THE LAND FOR 5 GENERATIONS</div>
  </div>
  <div class="back-label">
    <div class="back-title">HOLLOW MESA FARM</div>
    <div class="back-sub"><span>VAULT RESERVE</span><span>CABERNET SAUVIGNON</span></div>
    <div class="back-rule"></div>
    <p class="back-story">Hollow Mesa Farm wines are exclusively sourced from our family's Estate Vineyard in the Horse Heaven Hills of Washington state. For five generations, we have cultivated this rugged and fertile land, embodying our deep-seated love and dedication. We believe that exceptional wine is the result of outstanding vineyards, limited production, and astute winemaking. With the utmost pride and joy, we present this exquisite Cabernet Sauvignon from our ranch to your table.</p>
    <p class="signoff" style="top:226px">Cheers, <span class="sig">Mara Lindqvist</span><br>Mara Lindqvist, Winemaker</p>
    <p class="signoff" style="top:269px">Cheers, <span class="sig">Tom Hadley</span><br>Tom Hadley, Farmer &amp; Proprietor</p>
    <div class="crest" role="img" aria-label="Family crest illustration"></div>
    <div class="legal-panel">
      <p class="warning"><b>Government warning:</b> (1) According to the Surgeon General, women should not drink alcoholic beverages during pregnancy because of the risk of birth defects. (2) Consumption of alcoholic beverages impairs your ability to drive a car or operate machinery, and may cause health problems.</p>
      <div class="legal-right"><b>750 ML</b> contains sulfites<br>15% alc. by vol.<p class="produced"><b>Produced and bottled by:</b> Hadley Wine Estates, LLC, Prosser WA, USA</p></div>
      <div class="barcode-slot">Bar code placeholder</div>
    </div>
  </div>
</section>

<section class="option bg-cream ink-black">
  <p class="option-caption" style="left:56px">option 3: cream background, silver lettering with black accents</p>
  <div class="bottle-scene" role="img" aria-label="Photo of the wine bottle wearing the label on a wooden table"></div>
  <div class="front-label">
    <div class="front-frame"></div>
    <div class="line brand-name" style="top:66px">Hollow Mesa</div>
    <div class="line brand-name" style="top:117px">Farm</div>
    <div class="line estate" style="top:174px">ESTATE VINEYARD</div>
    <div class="line tier-script" style="top:203px">Vault Reserve</div>
    <div class="mark">Hollow<br>Mesa<br>Farm</div>
    <div class="line varietal" style="top:438px;color:var(--silver-ink)">CABERNET SAUVIGNON</div>
    <div class="line region" style="top:474px">HORSE HEAVEN HILLS</div>
    <div class="line vintage" style="top:494px">2022</div>
    <div class="heritage-band">FAMILY STEWARDS OF THE LAND FOR 5 GENERATIONS</div>
  </div>
  <div class="back-label">
    <div class="back-title">HOLLOW MESA FARM</div>
    <div class="back-sub"><span>VAULT RESERVE</span><span>CABERNET SAUVIGNON</span></div>
    <div class="back-rule"></div>
    <p class="back-story">Hollow Mesa Farm wines are exclusively sourced from our family's Estate Vineyard in the Horse Heaven Hills of Washington state. For five generations, we have cultivated this rugged and fertile land, embodying our deep-seated love and dedication. We believe that exceptional wine is the result of outstanding vineyards, limited production, and astute winemaking. With the utmost pride and joy, we present this exquisite Cabernet Sauvignon from our ranch to your table.</p>
    <p class="signoff" style="top:226px">Cheers, <span class="sig">Mara Lindqvist</span><br>Mara Lindqvist, Winemaker</p>
    <p class="signoff" style="top:269px">Cheers, <span class="sig">Tom Hadley</span><br>Tom Hadley, Farmer &amp; Proprietor</p>
    <div class="crest" role="img" aria-label="Family crest illustration"></div>
    <div class="legal-panel">
      <p class="warning"><b>Government warning:</b> (1) According to the Surgeon General, women should not drink alcoholic beverages during pregnancy because of the risk of birth defects. (2) Consumption of alcoholic beverages impairs your ability to drive a car or operate machinery, and may cause health problems.</p>
      <div class="legal-right"><b>750 ML</b> contains sulfites<br>15% alc. by vol.<p class="produced"><b>Produced and bottled by:</b> Hadley Wine Estates, LLC, Prosser WA, USA</p></div>
      <div class="barcode-slot">Bar code placeholder</div>
    </div>
  </div>
</section>

<section class="option bg-cream ink-silver">
  <p class="option-caption">option 4: cream background, all silver lettering</p>
  <div class="bottle-scene" role="img" aria-label="Photo of the wine bottle wearing the label on a wooden table"></div>
  <div class="front-label">
    <div class="front-frame"></div>
    <div class="line brand-name" style="top:66px">Hollow Mesa</div>
    <div class="line brand-name" style="top:117px">Farm</div>
    <div class="line estate" style="top:174px">ESTATE VINEYARD</div>
    <div class="line tier-script" style="top:203px">Vault Reserve</div>
    <div class="mark">Hollow<br>Mesa<br>Farm</div>
    <div class="line varietal" style="top:438px">CABERNET SAUVIGNON</div>
    <div class="line region" style="top:474px">HORSE HEAVEN HILLS</div>
    <div class="line vintage" style="top:494px">2022</div>
    <div class="heritage-band">FAMILY STEWARDS OF THE LAND FOR 5 GENERATIONS</div>
  </div>
  <div class="back-label">
    <div class="back-title">HOLLOW MESA FARM</div>
    <div class="back-sub"><span>VAULT RESERVE</span><span>CABERNET SAUVIGNON</span></div>
    <div class="back-rule"></div>
    <p class="back-story">Hollow Mesa Farm wines are exclusively sourced from our family's Estate Vineyard in the Horse Heaven Hills of Washington state. For five generations, we have cultivated this rugged and fertile land, embodying our deep-seated love and dedication. We believe that exceptional wine is the result of outstanding vineyards, limited production, and astute winemaking. With the utmost pride and joy, we present this exquisite Cabernet Sauvignon from our ranch to your table.</p>
    <p class="signoff" style="top:226px">Cheers, <span class="sig">Mara Lindqvist</span><br>Mara Lindqvist, Winemaker</p>
    <p class="signoff" style="top:269px">Cheers, <span class="sig">Tom Hadley</span><br>Tom Hadley, Farmer &amp; Proprietor</p>
    <div class="crest" role="img" aria-label="Family crest illustration"></div>
    <div class="legal-panel">
      <p class="warning"><b>Government warning:</b> (1) According to the Surgeon General, women should not drink alcoholic beverages during pregnancy because of the risk of birth defects. (2) Consumption of alcoholic beverages impairs your ability to drive a car or operate machinery, and may cause health problems.</p>
      <div class="legal-right"><b>750 ML</b> contains sulfites<br>15% alc. by vol.<p class="produced"><b>Produced and bottled by:</b> Hadley Wine Estates, LLC, Prosser WA, USA</p></div>
      <div class="barcode-slot">Bar code placeholder</div>
    </div>
  </div>
</section>

</main>
</body>
</html>
```